Flyer to Restuarant

This is for a new Jamaican restaurant called Mango Harbour Kitchen. It should have beach scene with coconut trees. pictures of jerk chicken, oxtails and fish platters. The Jamaican flag or The flyer should the colors of the jamaican flag. Black, green and yellow. Feel free to input own ideas.

Industry/Entity Type

Restaurant

Requirements
Must have
• It should have beach scene with coconut trees in the daytime. pictures of jerk chicken, oxtails and fish platters. The Jamaican flag or The flyer should the colors of the jamaican flag. Black, green and yellow.

```html
<!DOCTYPE html>
<html lang="en">
<head>
<meta charset="utf-8">
<title>Mango Harbour Kitchen – Flyer</title>
<link href="https://fonts.googleapis.com/css2?family=Archivo+Black&family=Arimo:wght@400;700&display=swap" rel="stylesheet">
<style>
  :root {
    --page-bg: #e9e4dc;
    --flyer-black: #0b0b0b;
    --jam-green: #7cc242;
    --jam-yellow: #f2ea12;
    --band-grey: #4a4a4a;
    --oval-white: #ffffff;
    --sky: #7fb6e6;
    --sea: #5fc2c8;
    --sand: #e8e2d2;
    --palm: #3d5a2a;
    --text-dark: #111111;
  }
  * { box-sizing: border-box; margin: 0; padding: 0; }
  html, body { width: 1200px; height: 900px; overflow: hidden; }
  body {
    background: var(--page-bg);
    font-family: "Arimo", Arial, sans-serif;
    position: relative;
  }
  .flyer {
    position: absolute;
    left: 300px; top: 26px;
    width: 600px; height: 848px;
    background: var(--flyer-black);
    overflow: hidden;
    box-shadow: 0 6px 18px rgba(0,0,0,.25);
  }
  .flyer-shapes { position: absolute; inset: 0; }
  .brand-oval {
    position: absolute;
    left: 352px; top: 118px;
    width: 280px; height: 150px;
    border-radius: 50%;
    background: var(--oval-white);
  }
  .brand-name {
    position: absolute;
    left: 362px; top: 165px;
    width: 230px;
    font-family: "Archivo Black", "Arial Black", sans-serif;
    font-weight: 400;
    font-size: 20px; line-height: 1.15;
    color: var(--jam-green);
    text-align: center;
    text-transform: uppercase;
  }
  .headline {
    position: absolute;
    left: 28px; top: 430px;
    width: 276px;
    font-weight: 700; font-size: 23px; line-height: 1.2;
    color: var(--jam-yellow);
    text-align: center;
  }
  .intro {
    position: absolute;
    left: 74px; top: 492px;
    width: 226px;
    font-size: 12px; line-height: 1.5;
    color: var(--jam-green);
  }
  .accent-squares {
    position: absolute;
    left: 20px; top: 600px;
    width: 44px; height: 28px;
    display: flex;
  }
  .accent-squares span { flex: 1; }
  .accent-squares .sq-green { background: var(--jam-green); }
  .accent-squares .sq-yellow { background: var(--jam-yellow); }
  .dish {
    position: absolute;
    border-radius: 12px;
    border: 3px solid var(--flyer-black);
  }
  .dish-oxtail {
    left: 316px; top: 420px; width: 156px; height: 104px;
    background: radial-gradient(ellipse at 50% 55%, #5a2c14 0 38%, #f4f1ec 40% 62%, #c9b79d 64%);
  }
  .dish-jerk {
    left: 472px; top: 476px; width: 124px; height: 116px;
    background: radial-gradient(ellipse at 55% 60%, #a65a24 0 35%, #6b3413 50%, #d8b34a 70%, #3a2a12);
  }
  .dish-fish {
    left: 312px; top: 570px; width: 156px; height: 112px;
    background: radial-gradient(ellipse at 45% 50%, #c9a47a 0 22%, #d8423a 30%, #6fae4a 48%, #eef0ea 66%, #2a2a2a);
  }
  .contact {
    position: absolute;
    left: 322px; top: 752px;
    font-weight: 700; font-size: 19px; line-height: 1.45;
    color: var(--text-dark);
  }
</style>
</head>
<body>
  <main class="flyer">
    <svg class="flyer-shapes" width="600" height="848" viewBox="0 0 600 848" aria-hidden="true">
      <defs>
        <linearGradient id="beachTones" x1="0" y1="0" x2="0.6" y2="1">
          <stop offset="0" stop-color="var(--sky)"/>
          <stop offset="0.35" stop-color="var(--palm)"/>
          <stop offset="0.65" stop-color="var(--sea)"/>
          <stop offset="1" stop-color="var(--sand)"/>
        </linearGradient>
      </defs>
      <path d="M0 0 H600 V464 C500 444 380 434 260 429 C150 424 90 204 0 204 Z" fill="var(--jam-yellow)"/>
      <path d="M0 0 H600 V446 C500 426 380 416 260 411 C150 406 90 186 0 186 Z" fill="var(--flyer-black)"/>
      <path d="M0 0 H600 V440 C500 420 380 410 260 405 C150 400 90 180 0 180 Z" fill="var(--jam-green)"/>
      <path d="M0 0 H600 V420 C500 400 380 390 260 385 C150 380 90 160 0 160 Z" fill="url(#beachTones)" role="img" aria-label="Daytime beach with coconut palm trees, white sand and turquoise sea"/>
      <path d="M0 700 C160 660 380 690 600 760 V848 H0 Z" fill="var(--band-grey)"/>
      <path d="M0 708 C160 672 380 700 600 772 V848 H0 Z" fill="var(--jam-green)"/>
      <path d="M0 722 C160 690 380 716 600 790 V848 H0 Z" fill="var(--jam-yellow)"/>
    </svg>

    <div class="brand-oval"></div>
    <h1 class="brand-name">Mango<br>Harbour Kitchen</h1>

    <h2 class="headline">Your Beutiful Headline Goes Here</h2>
    <p class="intro">Lorem Ipsum is simply dummy text of the printing and typesetting industry. Lorem Ipsum has been the industry's standard dummy text ever since the 1500s, when an unknown printer took a galley of type and scrambled it to make a type specimen book. It has survived not only five centuries, but also the leap into electronic typesetting, remaining essentially unchanged.</p>

    <div class="accent-squares" aria-hidden="true"><span class="sq-green"></span><span class="sq-yellow"></span></div>

    <div class="dish dish-oxtail" role="img" aria-label="Plate of braised oxtail"></div>
    <div class="dish dish-jerk" role="img" aria-label="Grilled jerk chicken"></div>
    <div class="dish dish-fish" role="img" aria-label="Fish platter with fresh salad"></div>

    <p class="contact">Contact Us : 000-0000-000<br>www.yoursitename.com</p>
  </main>
</body>
</html>
```